Merry Meadow Roasters

We need a website to sell coffee with a horse theme. We already have a logo and have designed 4 different coffee bags/flavors so far, each of which will be available in ground or whole bean. The brand is intended to be light hearted/whimsical.

Requirements
Must have
• incorporation of attached photos
Nice to have
• underlying background theme with sky/grass

```html
<!DOCTYPE html>
<html lang="en">
<head>
<meta charset="utf-8">
<title>Merry Meadow Roasters</title>
<link href="https://fonts.googleapis.com/css2?family=Playfair+Display:ital,wght@1,500;1,600;1,700&family=Roboto:ital,wght@0,400;0,500;0,700;1,400;1,700&display=swap" rel="stylesheet">
<style>
:root{
  --accent:#e0a36a;
  --accent-dark:#c98a4f;
  --brown:#3a2418;
  --ink:#2b2b2b;
  --muted:#5a5a5a;
  --cream:#f9ece0;
  --panel:#f2f0ee;
  --white:#ffffff;
}
*{margin:0;padding:0;box-sizing:border-box}
html,body{width:1200px;height:4242px;overflow:hidden;background:var(--white)}
body{font-family:"Roboto",sans-serif;color:var(--ink);position:relative}
.abs{position:absolute}
.kicker{font-family:"Roboto",sans-serif;font-style:italic;color:var(--accent);font-size:25px;text-align:center}
.title{font-family:"Playfair Display",serif;font-style:italic;font-weight:500;color:var(--brown);font-size:37px;text-align:center}
.btn{display:flex;align-items:center;justify-content:center;border-radius:30px;font-size:15px;font-weight:700;letter-spacing:.3px;text-transform:uppercase}
.btn-fill{background:var(--accent);color:var(--brown)}
.btn-line{border:1.5px solid var(--ink);color:var(--ink);background:var(--white)}

.topbar{left:0;top:0;width:1200px;height:44px;background:var(--cream);font-size:13px;color:var(--ink)}
.topbar .loc{left:111px;top:14px}
.topbar .ship{left:510px;top:14px}
.socials{left:953px;top:10px;display:flex;gap:5px}
.socials span{width:23px;height:23px;border:1.5px solid var(--ink);border-radius:50%}

.logo-badge{left:111px;top:30px;width:134px;height:134px;border-radius:50%;background:var(--white);display:flex;align-items:center;justify-content:center;text-align:center;z-index:3;font-size:16px;font-weight:700;color:var(--brown);line-height:1.2}
.search{left:304px;top:64px;width:600px;height:34px;border:1.5px solid #9a9a9a;border-radius:20px;font-size:13px;color:#777;padding:9px 18px}
.search .go{position:absolute;right:3px;top:3px;width:108px;height:25px;background:var(--accent);border-radius:14px;display:flex;align-items:center;justify-content:center;gap:8px;color:var(--brown)}
.icons{left:984px;top:68px;display:flex;gap:13px}
.icons span{width:26px;height:26px;border-radius:50%;background:var(--accent)}
.nav{left:0;top:115px;width:1200px;height:56px;background:var(--accent)}
.nav ul{list-style:none;display:flex;position:absolute;left:300px;top:19px;font-size:15px;color:var(--brown)}
.nav li{margin-right:40px}
.nav li.active{text-decoration:underline}

.hero{left:0;top:171px;width:1200px;height:583px;background:radial-gradient(ellipse at 25% 65%,#7a4a26 0%,#3b2414 45%,#1c110a 100%)}
.hero h1{position:absolute;right:32px;top:148px;font-family:"Playfair Display",serif;font-style:italic;font-weight:700;font-size:64px;color:var(--accent)}
.hero p{position:absolute;left:595px;top:240px;width:495px;text-align:center;font-style:italic;font-weight:700;font-size:27px;color:var(--white);line-height:1.25}
.hero .btn{position:absolute;left:741px;top:332px;width:205px;height:38px;font-size:14px}

.product{width:244px}
.bag{width:244px;height:365px;border-radius:4px;background:linear-gradient(180deg,#2a2622 0%,#efe4d4 22%,#e6d6be 75%,#3a2a1e 100%)}
.product h3{font-family:"Playfair Display",serif;font-style:italic;font-weight:500;font-size:26px;color:var(--brown);text-align:center;margin-top:36px;white-space:nowrap}
.product .btn{width:171px;height:38px;margin:18px auto 0;font-size:14px}

.about{left:0;top:1494px;width:1200px;height:591px;background:var(--panel)}
.about .art{position:absolute;left:110px;top:80px;width:490px;height:420px;border-radius:8px;background:radial-gradient(circle at 50% 60%,#f4dcc2 0%,#efe4d9 55%,var(--panel) 80%)}
.about .kicker{position:absolute;right:111px;top:98px;text-align:right}
.about h2{position:absolute;right:111px;top:136px;width:420px;text-align:right;font-family:"Playfair Display",serif;font-style:italic;font-weight:500;font-size:37px;line-height:1.12;color:var(--brown)}
.about .p1{position:absolute;right:111px;top:237px;width:470px;text-align:right;font-size:15px;line-height:26px}
.about .p2{position:absolute;right:111px;top:352px;width:490px;text-align:right;font-size:13.5px;line-height:26px;color:var(--muted)}
.about .btn{position:absolute;left:883px;top:450px;width:206px;height:40px}

.ph{border-radius:10px}
.ph-a{background:linear-gradient(160deg,#8a5a4a,#5a2c2c 50%,#b29a5a)}
.ph-b{background:radial-gradient(circle at 50% 60%,#8a5630,#3a2416 70%)}
.ph-c{background:linear-gradient(150deg,#c9c9c9,#5b5b5b 60%,#2a2a2a)}
.ph-d{background:linear-gradient(150deg,#3a3836,#c59a6a 50%,#e9e5e0)}
.ph-e{background:radial-gradient(circle at 40% 50%,#b48a5c,#3a2214 75%)}
.ph-f{background:linear-gradient(160deg,#2a2420,#d6cdc5 55%,#5a3a24)}

.offer{left:51px;top:2882px;width:1096px;height:389px;border-radius:24px;overflow:hidden;background:linear-gradient(90deg,#1b140f 0%,#2c231d 55%,#4a3426 80%,#2a1f18 100%)}
.offer .kick{position:absolute;left:60px;top:59px;font-style:italic;font-weight:700;font-size:25px;color:var(--accent)}
.offer h2{position:absolute;left:60px;top:98px;font-family:"Playfair Display",serif;font-style:italic;font-weight:700;font-size:40px;color:var(--white);letter-spacing:.5px}
.offer p{position:absolute;left:60px;top:160px;width:520px;font-style:italic;font-size:14px;line-height:26px;color:var(--white)}
.offer .btn{position:absolute;left:60px;top:252px;width:206px;height:38px}

.card{top:3506px;width:331px;height:282px;border:1.5px solid #e2e2e2;border-radius:12px;background:var(--white);text-align:center}
.avatar{position:absolute;left:125px;top:-42px;width:82px;height:82px;border-radius:50%;background:linear-gradient(160deg,#6b4a36,#2a1c14)}
.card h4{margin-top:56px;font-size:16px;font-weight:500}
.card .role{margin-top:12px;font-size:14px;color:var(--accent)}
.card p{margin:10px auto 0;width:300px;font-size:13.5px;line-height:22px;color:var(--muted)}
.stars{position:absolute;left:0;right:0;bottom:28px;color:#f2a400;font-size:19px;letter-spacing:2px}
.arrow{width:18px;height:18px;border-radius:50%;top:3638px;display:flex;align-items:center;justify-content:center;color:var(--white);font-size:12px;z-index:2}

.footer{left:0;top:3860px;width:1200px;height:382px;background:var(--panel)}
.footer .flogo{position:absolute;left:110px;top:100px;width:250px;text-align:center;font-weight:700;font-size:30px;color:var(--brown);line-height:1.2}
.fcol{position:absolute;top:80px}
.fcol h5{font-family:"Playfair Display",serif;font-style:italic;font-weight:500;font-size:26px;color:var(--brown);margin-bottom:14px}
.fcol li{list-style:none;font-size:14.5px;line-height:26px}
.contact li{display:flex;align-items:center;gap:18px;line-height:41px}
.footer .copy{position:absolute;left:431px;top:337px;font-size:14.5px}
</style>
</head>
<body>

<div class="abs topbar">
  <div class="abs loc">United States | USD $ &nbsp;⌄ &nbsp;&nbsp;|&nbsp;&nbsp; English &nbsp;⌄</div>
  <div class="abs ship">FREE SHIPPING | 100-DAY EASY RETURNS</div>
  <div class="abs socials"><span></span><span></span><span></span><span></span><span></span></div>
</div>

<div class="abs logo-badge">Merry Meadow<br>Roasters</div>
<div class="abs search">Search<div class="go">
  <svg width="12" height="12" viewBox="0 0 12 12"><circle cx="5" cy="5" r="3.8" fill="none" stroke="#3a2418" stroke-width="1.6"/><line x1="8" y1="8" x2="11" y2="11" stroke="#3a2418" stroke-width="1.6"/></svg>Search</div></div>
<div class="abs icons"><span></span><span></span><span></span></div>

<nav class="abs nav"><ul>
  <li class="active">HOME</li><li>ABOUT</li><li>OUR PRODUCTS &nbsp;⌄</li><li>SHOP NOW</li><li>LASTEST NEWS</li><li>FAQ</li><li>CONTACT US</li>
</ul></nav>

<section class="abs hero" role="img" aria-label="Dark mug of coffee on a wooden board surrounded by roasted beans">
  <h1>Coffee with a Kick.</h1>
  <p>Bold Brews for Wild Spirits—Fuel Your Ride with Every Sip!</p>
  <div class="btn btn-fill">View our products</div>
</section>

<div class="abs kicker" style="left:0;top:808px;width:1200px">Our Products</div>
<h2 class="abs title" style="left:0;top:842px;width:1200px">Merry Meadow Roasters.</h2>

<div class="abs product" style="left:67px;top:927px"><div class="bag" role="img" aria-label="Trail blazer coffee bag"></div><h3>Trail blazer</h3><div class="btn btn-line">Add to cart</div></div>
<div class="abs product" style="left:341px;top:927px"><div class="bag" role="img" aria-label="Dainty dancer coffee bag"></div><h3>Dainty dancer</h3><div class="btn btn-line">Add to cart</div></div>
<div class="abs product" style="left:614px;top:927px"><div class="bag" role="img" aria-label="Hay bale blend coffee bag"></div><h3>Hay bale blend</h3><div class="btn btn-fill">Add to cart</div></div>
<div class="abs product" style="left:887px;top:927px"><div class="bag" role="img" aria-label="Gallop n go coffee bag"></div><h3>Gallop n go</h3><div class="btn btn-line">Add to cart</div></div>

<section class="abs about">
  <div class="art" role="img" aria-label="Illustration of the brand name above a latte cup with coffee beans and leaves"></div>
  <div class="kicker">About Us – Merry Meadow Roasters</div>
  <h2>Brewing Adventure, One Cup at a Time.</h2>
  <p class="p1">At Merry Meadow Roasters, we believe that life (and coffee) should be bold, fun, and full of adventure. Born from a love of rich, flavorful coffee and the untamed spirit of the horse, we set out to create a brand that blends top-quality beans with a lighthearted twist.</p>
  <p class="p2">Our carefully crafted roasts are designed to keep you in the saddle—whether you're riding into a busy day, hitting the trails, or simply enjoying a slow morning by the fire.</p>
  <div class="btn btn-fill">Shop now</div>
</section>

<div class="abs kicker" style="left:0;top:2146px;width:1200px">Process</div>
<h2 class="abs title" style="left:0;top:2182px;width:1200px">Merry Meadow Roasters</h2>

<div class="abs ph ph-a" style="left:117px;top:2271px;width:308px;height:210px" role="img" aria-label="Coffee cherries drying on raised beds"></div>
<div class="abs ph ph-d" style="left:117px;top:2500px;width:308px;height:303px" role="img" aria-label="Barista handing over a paper takeaway bag"></div>
<div class="abs ph ph-b" style="left:448px;top:2271px;width:308px;height:302px" role="img" aria-label="Beans turning in a copper roaster"></div>
<div class="abs ph ph-e" style="left:448px;top:2594px;width:308px;height:209px" role="img" aria-label="Cup of coffee beside a scoop of beans"></div>
<div class="abs ph ph-c" style="left:774px;top:2271px;width:308px;height:256px" role="img" aria-label="Ground coffee filling an espresso portafilter"></div>
<div class="abs ph ph-f" style="left:774px;top:2546px;width:308px;height:257px" role="img" aria-label="Two cappuccinos being served on a wooden table"></div>

<section class="abs offer" role="img" aria-label="Steaming coffee cup on scattered beans against a dark background">
  <div class="kick">SPECIAL OFFER</div>
  <h2>SUMMER SALE</h2>
  <p>Join the herd and enjoy 10% off your first Merry Meadow Roasters purchase. Whether you like it bold and dark or smooth and mellow, there's a perfect roast waiting for you!</p>
  <div class="btn btn-fill">Shop now</div>
</section>

<div class="abs kicker" style="left:0;top:3348px;width:1200px">Testimonials</div>
<h2 class="abs title" style="left:0;top:3386px;width:1200px">Merry Meadow Roasters Reviews</h2>

<div class="abs arrow" style="left:76px;background:var(--brown)">‹</div>
<div class="abs arrow" style="left:1106px;background:var(--accent)">›</div>

<div class="abs card" style="left:87px"><div class="avatar" role="img" aria-label="Customer portrait"></div><h4>Owen Hartley</h4><div class="role">Business &nbsp;man</div><p>I've tried a lot of coffee, but nothing compares to Merry Meadow! Smooth, rich, and just the right kick to start my day. My mornings wouldn't be the same without it!</p><div class="stars">★★★★★</div></div>
<div class="abs card" style="left:438px"><div class="avatar" role="img" aria-label="Customer portrait"></div><h4>Reid P.</h4><div class="role">Business &nbsp;man</div><p>The smoothest coffee I've had in a long time. The flavors are well-balanced, and the packaging is adorable. Merry Meadow is now my go-to!</p><div class="stars">★★★★★</div></div>
<div class="abs card" style="left:787px"><div class="avatar" role="img" aria-label="Customer portrait"></div><h4>Clara V.</h4><div class="role">Business &nbsp;man</div><p>The branding caught my eye, but the flavor keeps me coming back. I love the playful horse theme, and the coffee is genuinely top-notch!</p><div class="stars">★★★★★</div></div>

<footer class="abs footer">
  <div class="flogo">Merry Meadow<br>Roasters</div>
  <div class="fcol" style="left:431px"><h5>Quick Links</h5><ul><li>Home</li><li>About us</li><li>Our products</li><li>Shop now</li><li>Lastest news</li><li>FAQ</li><li>Contact us</li></ul></div>
  <div class="fcol" style="left:619px"><h5>Our Products</h5><ul><li>Trail blazer</li><li>Dainty dancer</li><li>Hay bale blend</li><li>Gallop n go</li></ul></div>
  <div class="fcol contact" style="left:824px"><h5>Contact Us</h5><ul>
    <li><svg width="14" height="14" viewBox="0 0 14 14"><path d="M3 1l2.5 3-1.5 1.5c.8 1.8 2.2 3.2 4 4L9.5 8l3 2.5-1.5 2.5C6 13 1 8 1 2.5z" fill="#2b2b2b"/></svg>+1 555 014 2290</li>
    <li><svg width="14" height="11" viewBox="0 0 14 11"><rect x="0" y="0" width="14" height="11" rx="1" fill="#2b2b2b"/><path d="M1 1l6 5 6-5" stroke="#f2f0ee" stroke-width="1.2" fill="none"/></svg>hello@merrymeadow.example</li>
    <li><svg width="12" height="16" viewBox="0 0 12 16"><path d="M6 0a6 6 0 0 1 6 6c0 4-6 10-6 10S0 10 0 6a6 6 0 0 1 6-6z" fill="#2b2b2b"/><circle cx="6" cy="6" r="2.2" fill="#f2f0ee"/></svg>United States, Merry Meadow Roasters.</li>
  </ul></div>
  <div class="copy">© 2025 Merry Meadow Roasters. All Rights Reserved.</div>
</footer>

</body>
</html>
```